Telecommunications/Power civil contractor needs business card design

Were a new telecommunications/power underground civil contractor that is looking for a new business card design. Our company colours are silver or grey and orange. Feel free to use the white background logo or the black background logo.

Target Market(s)

Local contractors, utility companies, private sector mining/energy companies, developers.

Industry/Entity Type

Telecommunications

Contact Information for Business Card

Each card will need the following info:
Persons name:
Title:
E-mail:
Phone number:
Shop Address:
Mailing Address:

Requirements
Must have
• Each card will need the following info:
• Persons name:
• Title:
• E-mail:
• Phone number:
• Shop Address:
• Mailing Address:

```html
<!DOCTYPE html>
<html lang="en">
<head>
<meta charset="utf-8">
<title>Trench Line Civil Inc — Business Card</title>
<link rel="stylesheet" href="https://fonts.googleapis.com/css2?family=Open+Sans:wght@400;600;700;800&display=swap">
<style>
  :root {
    --bg: #cfcfcf;
    --card-black: #050505;
    --panel-black: #111111;
    --orange: #f05a23;
    --silver: #9a9a9a;
    --silver-light: #c4c4c4;
    --white: #ffffff;
  }
  * { box-sizing: border-box; margin: 0; padding: 0; }
  html, body {
    width: 1200px; height: 900px; overflow: hidden;
    background: var(--bg);
    font-family: "Open Sans", Arial, sans-serif;
  }
  .stage {
    width: 1200px; height: 900px;
    display: flex; flex-direction: column; align-items: center; justify-content: center;
    gap: 50px;
  }
  .card {
    position: relative;
    width: 600px; height: 343px;
    background: var(--card-black);
    overflow: hidden;
    box-shadow: 0 6px 18px rgba(0,0,0,0.25);
  }
  /* Front */
  .card-front { display: flex; align-items: center; justify-content: center; }
  .brand-panel {
    width: 300px; height: 200px;
    background: var(--panel-black);
    display: flex; flex-direction: column; align-items: center; justify-content: center;
    gap: 14px;
  }
  .brand-mark {
    width: 72px; height: 72px; border-radius: 50%;
    border: 6px solid var(--silver);
  }
  .brand-name {
    color: var(--orange);
    font-weight: 800; font-size: 24px; letter-spacing: 1px;
    text-transform: uppercase; text-align: center; line-height: 1.1;
  }
  /* Back */
  .card-back .swoosh { position: absolute; inset: 0; width: 600px; height: 343px; }
  .back-brand {
    position: absolute; left: 40px; top: 70px; width: 200px;
    display: flex; flex-direction: column; align-items: center; gap: 16px;
  }
  .back-brand .brand-mark { width: 130px; height: 130px; border-width: 10px; }
  .back-brand .brand-name { font-size: 17px; }
  .contact {
    position: absolute; right: 28px; top: 34px;
    color: var(--white); text-align: right;
    font-size: 14.5px; line-height: 20px;
  }
  .contact-name { font-weight: 700; font-size: 18px; line-height: 22px; }
  .contact-title { margin-bottom: 8px; }
  .contact-line { display: flex; justify-content: flex-end; align-items: center; gap: 8px; }
  .contact-line svg { width: 12px; height: 12px; fill: var(--white); }
  .contact-heading { font-weight: 700; margin-top: 6px; }
</style>
</head>
<body>
<main class="stage">
  <section class="card card-front" aria-label="Card front">
    <div class="brand-panel">
      <div class="brand-mark"></div>
      <div class="brand-name">Trench Line<br>Civil Inc</div>
    </div>
  </section>

  <section class="card card-back" aria-label="Card back">
    <svg class="swoosh" viewBox="0 0 600 343" aria-hidden="true">
      <path d="M300,0 C345,30 362,80 360,130 C356,210 310,285 215,343 L245,343 C330,290 378,215 382,130 C384,75 368,30 330,0 Z" fill="var(--silver)"/>
      <path d="M330,0 L600,0 L600,343 L245,343 C330,290 378,215 382,130 C384,75 368,30 330,0 Z" fill="var(--orange)"/>
    </svg>
    <div class="back-brand">
      <div class="brand-mark"></div>
      <div class="brand-name">Trench Line Civil Inc</div>
    </div>
    <div class="contact">
      <div class="contact-name">Marcus Reid</div>
      <div class="contact-title">Managing Director</div>
      <div class="contact-line">123.456.7890
        <svg viewBox="0 0 24 24"><path d="M6.6 10.8a15 15 0 0 0 6.6 6.6l2.2-2.2c.3-.3.7-.4 1-.2 1.1.4 2.3.6 3.6.6.6 0 1 .4 1 1V20c0 .6-.4 1-1 1C10.6 21 3 13.4 3 4c0-.6.4-1 1-1h3.5c.6 0 1 .4 1 1 0 1.3.2 2.5.6 3.6.1.3 0 .7-.2 1z"/></svg>
      </div>
      <div class="contact-line">info@youremail.com
        <svg viewBox="0 0 24 24"><path d="M2 5h20v14H2z M2 5l10 8 10-8" fill="var(--white)" stroke="var(--orange)" stroke-width="1.5"/></svg>
      </div>
      <div class="contact-heading">Mailing Address</div>
      <div>1234, Address Goes Here</div>
      <div>Country Name, 123456</div>
      <div class="contact-heading">Shop Address</div>
      <div>1234, Address Goes Here</div>
      <div>Country Name, 123456</div>
    </div>
  </section>
</main>
</body>
</html>
```